GivingGavelHub Website Redesign

I'm looking to give our website a new look and feel with better graphics/images and that is focused on conversions.
www.givinggavelhub.example. The content can stay the same. Im looking for a new hero section with maybe a call to auction form to create an auction by asking for the following information: Event Name, Event Benefits, Country, Time zone and currency.
Our goal is to show that we can host online auctions, mobile auctions and live in-person auction. The content does not need to change on the site. We just need sections or illustrations that represent those features. It would also be good to have a sections that will segment our users into the following categories: Nonprofits/Charities, Schools/Education, Businesses, Government Agency, Individual.
The following pages need to be updated:
https://www.givinggavelhub.example/
https://www.givinggavelhub.example/online-bidding-features
https://www.givinggavelhub.example/online-bidding-experience
https://www.givinggavelhub.example/about
https://www.givinggavelhub.example/pricing
Updates
This project would cover the following 4 pages:
https://www.givinggavelhub.example

```html
<!DOCTYPE html>
<html lang="en">
<head>
<meta charset="utf-8">
<title>GivingGavelHub – Online Charity Auctions</title>
<link rel="stylesheet" href="https://fonts.googleapis.com/css2?family=Poppins:wght@400;500;600;700&family=Roboto:wght@400;500&display=swap">
<style>
:root{
  --navy:#1c3f94;
  --blue:#2f7ff0;
  --faq:#0d47a8;
  --ink:#1e2533;
  --muted:#4a5160;
  --soft:#eef0f4;
  --white:#fff;
  --black:#0b0b0b;
  --star:#f5a623;
}
*{box-sizing:border-box;margin:0;padding:0}
html,body{width:1200px;height:4673px;overflow:hidden}
body{font-family:"Roboto",sans-serif;color:var(--ink);background:var(--white);position:relative}
h1,h2,h3,.btn,.brand{font-family:"Poppins",sans-serif}
section,header,footer{position:absolute;left:0;width:1200px}
.abs{position:absolute}

/* header */
.site-header{top:0;height:85px;background:rgba(45,45,45,.72);z-index:3}
.brand{position:absolute;display:flex;align-items:center;gap:10px;color:var(--white);font-weight:600;font-size:25px;letter-spacing:-.5px}
.brand .mark{width:30px;height:30px;border-radius:50%;background:var(--white)}
.site-header .brand{left:112px;top:26px}
.nav{position:absolute;left:567px;top:32px;display:flex;gap:26px;font-size:14px;color:#e6e6e6}
.search{position:absolute;left:914px;top:31px}
.signup{position:absolute;left:966px;top:22px;width:120px;height:42px;border-radius:21px;background:var(--blue);color:#fff;font:600 14px "Poppins",sans-serif;display:flex;align-items:center;justify-content:center}

/* hero */
.hero{top:0;height:598px}
.hero-art{position:absolute;inset:0;background:linear-gradient(90deg,#a7dcd2 0%,#7fc3bb 40%,#5ea6a4 60%,#c98b78 75%,#b8483e 82%,#5a9d9c 100%)}
.hero h1{position:absolute;left:100px;top:124px;width:470px;text-align:center;font-size:26px;line-height:40px;font-weight:600;color:var(--navy)}
.build-form{position:absolute;left:112px;top:226px;width:445px;height:322px;border:4px solid var(--blue);border-radius:30px;background:rgba(130,150,145,.82);padding:0 22px}
.build-form h2{text-align:center;color:var(--white);font-size:25px;font-weight:500;margin-top:20px;margin-bottom:18px}
.fields{display:grid;grid-template-columns:1fr 1fr;gap:16px 14px}
.field{height:44px;border-radius:22px;background:var(--white);font-size:12px;color:#888;display:flex;align-items:center;padding-left:22px}
.field.wide{grid-column:1/3}
.btn-create{margin-top:16px;height:46px;border-radius:23px;background:var(--blue);color:#fff;font-size:14px;font-weight:600;display:flex;align-items:center;justify-content:center}
.dots{position:absolute;display:flex;gap:7px}
.dots i{width:9px;height:9px;border-radius:50%;background:#c9ccd3;display:block}
.dots i.on{background:var(--navy)}
.hero .dots i{background:#fff}.hero .dots i.on{background:var(--navy)}

/* section titles */
.title{position:absolute;left:0;width:1200px;text-align:center;font-size:29px;font-weight:600;color:var(--navy)}
.title span{color:var(--blue)}

/* goal */
.goal{top:598px;height:550px}
.card{position:absolute;top:171px;width:298px;height:290px}
.card .photo{position:absolute;inset:0}
.card .tag{position:absolute;right:0;bottom:0;width:240px;height:50px;background:#fff;font:600 16px "Poppins",sans-serif;display:flex;align-items:center;padding-left:42px;clip-path:polygon(14% 0,100% 0,100% 100%,0 100%)}
.card .tag.active{background:var(--navy);color:#fff}

/* features */
.features{top:1148px;height:1579px;background:var(--soft)}
.feature{position:absolute;width:480px}
.feature h3{font-size:26px;line-height:43px;font-weight:500;color:var(--ink)}
.feature p{font-size:14px;line-height:25px;color:var(--muted);margin-top:16px}
.btn-pill{display:inline-flex;margin-top:22px;height:44px;padding:0 16px;border-radius:22px;background:var(--navy);color:#fff;font:600 14px "Poppins",sans-serif;align-items:center}
.quote{display:flex;gap:16px;margin-top:16px}
.avatar{width:52px;height:52px;border-radius:50%;flex:none;background:linear-gradient(135deg,#c99a80,#7a4a3c)}
.quote strong{font:500 15px "Poppins",sans-serif;display:block;margin-bottom:6px}
.quote p{margin:0;font-size:10.5px;line-height:17px;color:var(--ink)}
.stars{color:var(--star);font-size:10px;letter-spacing:1px}
.illus{position:absolute;border-radius:46% 54% 48% 52%/52% 46% 54% 48%}

/* categories */
.categories{top:2727px;height:411px}
.cat{position:absolute;top:163px;width:222px;height:163px;color:#fff;font:600 14px "Poppins",sans-serif;display:flex;flex-direction:column;align-items:center;justify-content:flex-end;padding-bottom:30px;gap:24px;box-shadow:0 3px 8px rgba(0,0,0,.12)}
.cat.dark{background:var(--navy)}.cat.light{background:var(--blue)}
.arrow{position:absolute;top:2950px}

/* faq */
.faq{top:3138px;height:747px;background:var(--faq)}
.faq .title{color:#fff;top:72px}
.q{position:absolute;left:234px;width:731px;background:#fff;padding:0 0 0 92px}
.q .ico{position:absolute;left:38px;top:26px}
.q h3{font-size:18px;font-weight:500;color:var(--ink);line-height:77px}
.q.open h3{color:var(--blue);line-height:1;padding-top:28px}
.q.open p{font-size:12px;line-height:25px;margin-top:14px;padding-right:40px}
.view-all{position:absolute;left:528px;top:629px;width:144px;height:44px;border-radius:22px;background:var(--blue);color:#fff;font:600 14px "Poppins",sans-serif;display:flex;align-items:center;justify-content:center}

/* partners */
.partners{top:3885px;height:419px}
.partners .sub{position:absolute;top:138px;width:1200px;text-align:center;font-size:14px;color:var(--muted)}
.partner{position:absolute;top:192px;width:212px;height:96px;border-radius:14px;background:#fff;box-shadow:0 3px 12px rgba(0,0,0,.14);display:flex;align-items:center;justify-content:center;font:600 15px "Poppins",sans-serif;color:var(--navy)}

/* footer */
.site-footer{top:4304px;height:369px;background:var(--black);color:#fff}
.site-footer .brand{left:0;width:1200px;justify-content:center;top:90px;font-size:38px;color:var(--blue)}
.site-footer .brand .mark{width:40px;height:40px;background:var(--blue)}
.contact{position:absolute;top:183px;display:flex;gap:20px;align-items:center}
.contact .circ{width:62px;height:62px;border-radius:50%;background:var(--blue);display:flex;align-items:center;justify-content:center}
.contact b{font:600 13px "Poppins",sans-serif;display:block;margin-bottom:4px}
.contact span{font-size:13px;line-height:19px;display:block}
.vline{position:absolute;top:178px;width:1px;height:74px;background:#444}
.site-footer .rule{position:absolute;left:112px;top:283px;width:976px;height:1px;background:#333}
.copy{position:absolute;top:315px;width:1200px;text-align:center;font-size:13px}
.social{position:absolute;left:986px;top:317px;display:flex;gap:14px}
.social i{width:11px;height:11px;border-radius:50%;background:var(--blue);display:block}
</style>
</head>
<body>

<header class="site-header">
  <div class="brand"><i class="mark"></i>GivingGavelHub</div>
  <nav class="nav"><span>How It Works</span><span>Pricing</span><span>About</span><span>Blog</span></nav>
  <svg class="search" width="20" height="20" viewBox="0 0 20 20" fill="none" stroke="#fff" stroke-width="2.4"><circle cx="8" cy="8" r="6"/><path d="M12.5 12.5 18 18"/></svg>
  <div class="signup">SIGN UP</div>
</header>

<section class="hero">
  <div class="hero-art" role="img" aria-label="Caring hands holding a red heart over a teal background"></div>
  <h1>You've just found the easiest online auction platform to use, period.</h1>
  <form class="build-form">
    <h2>BUILD AN AUCTION</h2>
    <div class="fields">
      <div class="field">Name your event</div>
      <div class="field">Event Benefits</div>
      <div class="field">Country*</div>
      <div class="field">Time Zone*</div>
      <div class="field wide">Currency*</div>
    </div>
    <div class="btn-create">CREATE NEW EVENT</div>
  </form>
  <div class="dots" style="left:578px;top:552px"><i></i><i class="on"></i><i></i></div>
</section>

<section class="goal">
  <h2 class="title" style="top:82px">OUR <span>GOAL</span></h2>
  <div class="card" style="left:110px">
    <div class="photo" role="img" aria-label="Friends celebrating while bidding on phones" style="background:linear-gradient(135deg,#b8542c,#d89a5a,#3a2a22)"></div>
    <div class="tag">Online auctions</div>
  </div>
  <div class="card" style="left:451px">
    <div class="photo" role="img" aria-label="Man cheering while bidding on his smartphone" style="background:linear-gradient(135deg,#5f88a6,#8fb2c8,#2c3e55)"></div>
    <div class="tag active">Mobile auctions</div>
  </div>
  <div class="card" style="left:790px">
    <div class="photo" role="img" aria-label="Woman celebrating at a laptop in a bright office" style="background:linear-gradient(135deg,#6d8a5a,#d9d4cc,#a28770)"></div>
    <div class="tag">Live in-person auctions</div>
  </div>
</section>

<section class="features">
  <h2 class="title" style="top:66px;font-size:28px">SPEND LESS TIME. <span>MAKE MORE MONEY.</span></h2>

  <div class="feature" style="left:110px;top:160px">
    <h3>Quickly create, design and<br>manage auctions.</h3>
    <p>You are only 5 minutes away from having your auction built and ready for items. We took the pain and confusion out of getting started.</p>
    <span class="btn-pill">BUILD AN AUCTION</span>
    <div class="quote"><div class="avatar" role="img" aria-label="Portrait of Marla B."></div><div><strong>Marla B. - Maple Civic Club</strong><p>"I'm 74 years old and I didn't need to call my Grandkids to set up this auction for me! The software was easy to use and the end of auction experience was a breeze!"</p><div class="stars">★★★★★</div></div></div>
  </div>
  <div class="illus" role="img" aria-label="Laptop showing a team collaborating on auction dashboards" style="left:600px;top:175px;width:470px;height:390px;background:radial-gradient(circle at 50% 45%,#2a8f9a 0,#3f5fa8 38%,#d5dbe6 40%,#dfe3ea 100%)"></div>

  <div class="illus" role="img" aria-label="Hand holding a tablet with a person working at a desk among charts" style="left:123px;top:629px;width:475px;height:408px;background:radial-gradient(circle at 50% 45%,#40b5c9 0,#5b7fd0 30%,#d5dbe6 34%,#dfe3ea 100%)"></div>
  <div class="feature" style="left:649px;top:629px">
    <h3>Quickly create, design and<br>manage auctions.</h3>
    <p>You are only 5 minutes away from having your auction built and ready for items. We took the pain and confusion out of getting started.</p>
    <span class="btn-pill">BUILD AN AUCTION</span>
    <div class="quote"><div class="avatar" role="img" aria-label="Portrait of Marla B."></div><div><strong>Marla B. - Maple Civic Club</strong><p>"I'm 74 years old and I didn't need to call my Grandkids to set up this auction for me! The software was easy to use and the end of auction experience was a breeze!"</p><div class="stars">★★★★★</div></div></div>
  </div>

  <div class="feature" style="left:110px;top:1099px">
    <h3>Manage your donors and<br>donations effortlessly.</h3>
    <p>Our Donation CRM allows you to easily track all donations and donors in an easy-to-use dashboard. Export all information or sync with our integration partners to unlock more donor management tools.</p>
    <span class="btn-pill">MANAGE MY DONORS</span>
    <div class="quote"><div class="avatar" role="img" aria-label="Portrait of Dan Rourke" style="background:linear-gradient(135deg,#a57a5e,#3f2c24)"></div><div><strong>Dan Rourke - Lakeland Rovers</strong><p>The people coming to our events say it's easy to use and we can check people out so much faster than we ever could in the past. I highly recommend trying GivingGavelHub out, you'll never go anywhere else.</p><div class="stars">★★★★★</div></div></div>
  </div>
  <div class="illus" role="img" aria-label="People organising donor records beside a large phone and city buildings" style="left:616px;top:1118px;width:472px;height:390px;background:radial-gradient(circle at 50% 50%,#3fae8f 0,#2f7ff0 30%,#d5dbe6 36%,#dfe3ea 100%)"></div>
</section>

<section class="categories">
  <h2 class="title" style="top:82px">OUR <span>CATEGORIES</span></h2>
  <div class="cat dark" style="left:112px">
    <svg width="74" height="64" viewBox="0 0 74 64" fill="none" stroke="#fff" stroke-width="2.5"><path d="M37 58 8 30a15 15 0 0 1 29-16 15 15 0 0 1 29 16Z"/><path d="M22 36l10 10M28 30l12 12M34 24l10 10"/></svg>NONPROFITS</div>
  <div class="cat light" style="left:364px">
    <svg width="80" height="64" viewBox="0 0 80 64" fill="none" stroke="#fff" stroke-width="2.5"><path d="M4 62h72M10 62V28h60v34M24 28V16h32v12M40 4v12M34 62V46h12v16"/><circle cx="40" cy="36" r="5"/><path d="M16 36h6M58 36h6M16 48h6M58 48h6"/></svg>SCHOOLS</div>
  <div class="cat dark" style="left:616px">
    <svg width="72" height="68" viewBox="0 0 72 68" fill="none" stroke="#fff" stroke-width="2.5"><rect x="8" y="4" width="40" height="36"/><path d="M16 14h24M16 22h24"/><rect x="14" y="34" width="48" height="30" rx="3"/><path d="M30 34v-6h16v6M14 46h48"/><circle cx="60" cy="14" r="7"/></svg>BUSINESSES</div>
  <div class="cat light" style="left:867px">
    <svg width="80" height="66" viewBox="0 0 80 66" fill="none" stroke="#fff" stroke-width="2.5"><rect x="26" y="6" width="28" height="34"/><path d="M32 14h4M44 14h4M32 22h4M44 22h4M32 30h4M44 30h4"/><circle cx="18" cy="46" r="7"/><circle cx="40" cy="46" r="7"/><circle cx="62" cy="46" r="7"/><path d="M6 64v-4a12 6 0 0 1 24 0v4M28 64v-4a12 6 0 0 1 24 0v4M50 64v-4a12 6 0 0 1 24 0v4"/></svg>GOVERNMENT AGENCIES</div>
</section>
<svg class="arrow" style="left:68px" width="16" height="26" viewBox="0 0 16 26" fill="none" stroke="#2f7ff0" stroke-width="2.5"><path d="M14 2 3 13l11 11"/></svg>
<svg class="arrow" style="left:1116px" width="16" height="26" viewBox="0 0 16 26" fill="none" stroke="#1c3f94" stroke-width="2.5"><path d="M2 2l11 11L2 24"/></svg>

<section class="faq">
  <h2 class="title">FREQUENTLY ASKED QUESTIONS</h2>
  <div class="q" style="top:152px;height:77px">
    <svg class="ico" width="26" height="26" viewBox="0 0 26 26" stroke="#1e2533" stroke-width="2.4"><path d="M13 1v24M1 13h24"/></svg>
    <h3>Can I Pass Fees Onto Bidders?</h3></div>
  <div class="q" style="top:252px;height:77px">
    <svg class="ico" width="26" height="26" viewBox="0 0 26 26" stroke="#1e2533" stroke-width="2.4"><path d="M13 1v24M1 13h24"/></svg>
    <h3>What Happens If Items Don't Sell?</h3></div>
  <div class="q open" style="top:345px;height:145px">
    <svg class="ico" width="26" height="26" viewBox="0 0 26 26" stroke="#2f7ff0" stroke-width="3"><path d="M1 13h24"/></svg>
    <h3>Can I Download All My Bidder Data?</h3>
    <p>Yes, you can download any data we collect. It's a great way to keep your donor management database up to date. Also, check out our integrations to see if we can auto-update your donor management tools.</p></div>
  <div class="q" style="top:506px;height:77px">
    <svg class="ico" width="26" height="26" viewBox="0 0 26 26" stroke="#1e2533" stroke-width="2.4"><path d="M13 1v24M1 13h24"/></svg>
    <h3>What Is The Management Fee?</h3></div>
  <div class="view-all">VIEW ALL</div>
</section>

<section class="partners">
  <h2 class="title" style="top:92px">YOU'RE IN <span>GOOD COMPANY</span></h2>
  <p class="sub">Here are some other organizations that have run auctions with us</p>
  <div class="partner" style="left:110px">Harbor Youth League</div>
  <div class="partner" style="left:364px">Lakeshore University</div>
  <div class="partner" style="left:620px">Ironside Athletics</div>
  <div class="partner" style="left:877px">Crestmoor College</div>
  <div class="dots" style="left:569px;top:323px"><i></i><i class="on"></i><i></i><i></i></div>
</section>

<footer class="site-footer">
  <div class="brand"><i class="mark"></i>GivingGavelHub</div>
  <div class="contact" style="left:148px">
    <div class="circ"><svg width="20" height="26" viewBox="0 0 20 26" fill="#fff"><path d="M10 0a10 10 0 0 0-10 10c0 7 10 16 10 16s10-9 10-16A10 10 0 0 0 10 0Zm0 14a4 4 0 1 1 0-8 4 4 0 0 1 0 8Z"/></svg></div>
    <div><b>ADDRESS :</b><span>Lorem ipsum dolor sit<br>amet, consectetur</span></div></div>
  <div class="vline" style="left:420px"></div>
  <div class="contact" style="left:477px">
    <div class="circ"><svg width="24" height="18" viewBox="0 0 24 18" fill="#fff"><path d="M0 0h24v18H0Z"/><path d="M1 1l11 9 11-9" fill="none" stroke="#2f7ff0" stroke-width="2"/></svg></div>
    <div><b>EMAIL :</b><span>info@givinggavelhub.example</span></div></div>
  <div class="vline" style="left:816px"></div>
  <div class="contact" style="left:856px">
    <div class="circ"><svg width="24" height="24" viewBox="0 0 24 24" fill="#fff"><path d="M5 1l4 5-2.5 3a14 14 0 0 0 8.5 8.5L18 15l5 4-2 4C10 23 1 14 1 3Z"/></svg></div>
    <div><b>CALL US :</b><span>+1 (555) 010 0199</span></div></div>
  <div class="rule"></div>
  <p class="copy">© 2023 GivingGavelHub. All Rights Reserved</p>
  <div class="social"><i></i><i></i><i></i><i></i></div>
</footer>

</body>
</html>
```